Modern business card design for professional copywriter

I'd like a business card design that I can use to have my cards printed out by quillprint.com as a squared corners business card (see artwork and design guidelines here: https://help.quillprint.com/hc/en-gb/sections/200570950-QUILL-Product-Templates)

The design should be clean and modern and reflect the colours, tone and branding on my website: https://tessavorrin.com.au

Target Market(s)

Professionals, B2B small business owners

Industry/Entity Type

Business

Contact Information for Business Card

Tessa Vorrin
m: 0468 905 327
e: tessa@tessavorrin.com.au
w: tessavorrin.com.au

Font styles to use
Sans Serif

Requirements
Must have
• Tagline: "Smart copywriting for clever business people"
• Brand colours: fd8000, 009984, 666666 and black
Nice to have

```html
<!DOCTYPE html>
<html lang="en">
<head>
<meta charset="utf-8">
<title>Tessa Vorrin – Business Card</title>
<link rel="stylesheet" href="https://fonts.googleapis.com/css2?family=Arimo:wght@400;700&family=Montserrat:wght@400;500&display=swap">
<style>
  :root {
    --orange: #fd8000;
    --teal: #009984;
    --grey: #666666;
    --ink: #000000;
    --paper: #ffffff;
    --backdrop: #e4e6e8;
  }
  * { box-sizing: border-box; margin: 0; padding: 0; }
  html, body { width: 1200px; height: 1200px; overflow: hidden; }
  body {
    background: var(--backdrop);
    display: flex;
    flex-direction: column;
    align-items: center;
    justify-content: center;
    gap: 46px;
    font-family: "Arimo", Arial, sans-serif;
  }
  .card {
    position: relative;
    width: 760px;
    height: 497px;
    background: var(--paper);
    box-shadow: 0 2px 10px rgba(0,0,0,0.08);
  }

  /* Front */
  .card-front .brand {
    position: absolute;
    top: 170px;
    left: 0;
    right: 0;
    display: flex;
    justify-content: center;
    align-items: center;
    gap: 16px;
  }
  .brand-mark {
    width: 30px;
    height: 30px;
    background: var(--teal);
  }
  .brand-name {
    font-family: "Montserrat", Arial, sans-serif;
    font-weight: 500;
    font-size: 54px;
    color: var(--teal);
    letter-spacing: -0.5px;
  }
  .tagline {
    position: absolute;
    top: 305px;
    left: 0;
    right: 0;
    text-align: center;
    font-size: 25px;
    color: var(--ink);
  }

  /* Back */
  .portrait {
    position: absolute;
    left: 208px;
    top: 170px;
    width: 176px;
    height: 176px;
    border-radius: 50%;
    border: 4px solid var(--teal);
    background: radial-gradient(circle at 50% 40%, #e8d6c4 0%, #d9cbb8 35%, #8a7d70 75%, #4f4a46 100%);
  }
  .divider {
    position: absolute;
    left: 415px;
    top: 130px;
    width: 3px;
    height: 250px;
    background: var(--teal);
  }
  .contact-list {
    position: absolute;
    left: 445px;
    top: 168px;
    list-style: none;
    display: flex;
    flex-direction: column;
    gap: 22px;
  }
  .contact-item {
    display: flex;
    align-items: center;
    gap: 16px;
    font-family: "Montserrat", Arial, sans-serif;
    font-size: 17px;
    color: var(--grey);
    letter-spacing: 0.5px;
  }
  .contact-icon {
    width: 36px;
    height: 36px;
    display: flex;
    align-items: center;
    justify-content: center;
    background: var(--teal);
  }
  .contact-icon.is-web { background: var(--orange); }
  .contact-icon svg { width: 20px; height: 20px; }
</style>
</head>
<body>
  <section class="card card-front">
    <div class="brand">
      <span class="brand-mark"></span>
      <span class="brand-name">Tessa Vorrin</span>
    </div>
    <p class="tagline">Smart copywriting for clever business people</p>
  </section>

  <section class="card card-back">
    <div class="portrait" role="img" aria-label="Portrait photograph of Tessa Vorrin"></div>
    <div class="divider"></div>
    <ul class="contact-list">
      <li class="contact-item">
        <span class="contact-icon is-phone">
          <svg viewBox="0 0 24 24"><path fill="#fff" d="M6.6 10.8a15.1 15.1 0 0 0 6.6 6.6l2.2-2.2c.3-.3.7-.4 1-.2 1.1.4 2.3.6 3.6.6.6 0 1 .4 1 1V20c0 .6-.4 1-1 1A17 17 0 0 1 3 4c0-.6.4-1 1-1h3.5c.6 0 1 .4 1 1 0 1.3.2 2.5.6 3.6.1.3 0 .7-.2 1z"/></svg>
        </span>
        <span class="contact-text">0468 905 327</span>
      </li>
      <li class="contact-item">
        <span class="contact-icon is-web">
          <svg viewBox="0 0 24 24" fill="none" stroke="#fff" stroke-width="1.8"><circle cx="12" cy="12" r="9"/><ellipse cx="12" cy="12" rx="4" ry="9"/><path d="M3 12h18M5 7h14M5 17h14"/></svg>
        </span>
        <span class="contact-text">tessavorrin.com.au</span>
      </li>
      <li class="contact-item">
        <span class="contact-icon is-mail">
          <svg viewBox="0 0 24 24" fill="none" stroke="#fff" stroke-width="1.8"><rect x="3" y="6" width="18" height="12"/><path d="M3 6l9 7 9-7"/></svg>
        </span>
        <span class="contact-text">tessa@tessavorrin.com.au</span>
      </li>
    </ul>
  </section>
</body>
</html>
```